Local Roofing/Construction company business needs new biz card design

We need a new business card design, current cards are from the start of this operation and generic at best. We are a local Construction Company (General Contractor) with a majority of our work originating from insurance claims-exterior finish work is the main focus (Roofs-Siding-Gutters etc). Heavily involved with homeowners and the low ball offers they receive from insurance company's after a insurable event takes place. I have attached some of our original logo file(s) below.

```html
<!DOCTYPE html>
<html lang="en">
<head>
<meta charset="utf-8">
<title>Ridgeline Construction – Business Card</title>
<link href="https://fonts.googleapis.com/css2?family=Montserrat:wght@400;500;700;800&display=swap" rel="stylesheet">
<style>
  :root {
    --brand-green: #58b56f;
    --brand-dark: #0f2027;
    --card-white: #ffffff;
    --text-grey: #4a4a4a;
    --backdrop-top: #cfcfcf;
    --backdrop-bottom: #9d9d9d;
  }
  * { margin: 0; padding: 0; box-sizing: border-box; }
  html, body { width: 1200px; height: 802px; overflow: hidden; }
  body {
    background: linear-gradient(180deg, var(--backdrop-top), var(--backdrop-bottom));
    font-family: "Montserrat", sans-serif;
    position: relative;
  }
  .card {
    position: absolute;
    width: 525px;
    height: 300px;
    border-radius: 22px;
    box-shadow: 0 14px 30px rgba(0,0,0,0.22);
    overflow: hidden;
  }
  .card--front { left: 50px; top: 251px; background: var(--card-white); }
  .card--back  { left: 625px; top: 251px; background: var(--brand-green); }

  .wordmark {
    display: flex;
    align-items: center;
    gap: 10px;
    font-weight: 800;
    text-transform: uppercase;
    letter-spacing: 1px;
    line-height: 1;
    white-space: nowrap;
  }
  .wordmark__square { width: 16px; height: 16px; flex: none; }

  .card--front .wordmark { position: absolute; left: 40px; top: 40px; color: var(--brand-green); font-size: 22px; }
  .card--front .wordmark__square { background: var(--brand-green); }

  .contact { position: absolute; left: 40px; top: 100px; color: var(--text-grey); }
  .contact__name {
    color: var(--brand-green);
    font-weight: 700;
    font-size: 20px;
    letter-spacing: 1px;
    text-transform: uppercase;
  }
  .contact__role { font-size: 13px; margin-top: 4px; }
  .contact__address { font-size: 13px; margin-top: 16px; line-height: 1.45; }
  .contact__list { list-style: none; margin-top: 14px; font-size: 13px; line-height: 1.55; }
  .contact__list li { display: flex; align-items: center; gap: 8px; }
  .contact__list svg { width: 11px; height: 11px; flex: none; }

  .accent-bar {
    position: absolute;
    left: 0; top: 212px;
    width: 22px; height: 34px;
    background: var(--brand-green);
  }

  .card--back .wordmark {
    position: absolute;
    left: 50%; top: 50%;
    transform: translate(-50%, -50%);
    color: var(--brand-dark);
    font-size: 24px;
    gap: 12px;
  }
  .card--back .wordmark__square { width: 20px; height: 20px; background: var(--brand-dark); }
</style>
</head>
<body>
  <section class="card card--front" aria-label="Business card front">
    <div class="wordmark"><span class="wordmark__square"></span>Ridgeline Construction</div>
    <div class="contact">
      <p class="contact__name">Calvin Mercer</p>
      <p class="contact__role">Managing Director</p>
      <p class="contact__address">418 Oakridge Avenue<br>Maple County 4470</p>
      <ul class="contact__list">
        <li>
          <svg viewBox="0 0 12 12"><path d="M2.5 1l2 2.5-1 1.2a6 6 0 0 0 3.8 3.8l1.2-1L11 9.5 9.8 11C5 11 1 7 1 2.2z" fill="var(--brand-green)"/></svg>
          0412 555 019
        </li>
        <li>
          <svg viewBox="0 0 12 12"><rect x="1" y="2.5" width="10" height="7" rx="1" fill="var(--brand-green)"/><path d="M1.5 3l4.5 3.5L10.5 3" stroke="#fff" fill="none"/></svg>
          info@ridgelinebuild.com
        </li>
        <li>
          <svg viewBox="0 0 12 12"><circle cx="6" cy="6" r="5" fill="var(--brand-green)"/><path d="M1 6h10M6 1c-2.5 3-2.5 7 0 10M6 1c2.5 3 2.5 7 0 10" stroke="#fff" stroke-width=".8" fill="none"/></svg>
          www.ridgelinebuild.com
        </li>
      </ul>
    </div>
    <span class="accent-bar"></span>
  </section>

  <section class="card card--back" aria-label="Business card back">
    <div class="wordmark"><span class="wordmark__square"></span>Ridgeline Construction</div>
  </section>
</body>
</html>
```